Business Card Design Project

Business Card
We are rebranding with a new logo
Industry/Entity Type
Business
Contact Information for Business Card
Dennis Morvale +61 487215963 dennis@quorv.com.au P.O. Box 872 Fernlow QLD 4309
Requirements
Must have
- Logo

```html
<!DOCTYPE html>
<html lang="en">
<head>
<meta charset="utf-8">
<title>Quorv International – Business Card</title>
<link href="https://fonts.googleapis.com/css2?family=Roboto:wght@400;500&family=Roboto+Condensed:wght@700&display=swap" rel="stylesheet">
<style>
  :root {
    --backdrop: #2b2b2b;
    --card: #f4f4f4;
    --brand-blue: #1a86c2;
    --brand-orange: #e97a1f;
    --text-grey: #555555;
    --rule-grey: #8a8a8a;
  }
  html, body {
    margin: 0;
    width: 1200px;
    height: 960px;
    overflow: hidden;
    background: var(--backdrop);
  }
  .business-card {
    position: absolute;
    left: 223px;
    top: 265px;
    width: 754px;
    height: 430px;
    background: var(--card);
    font-family: "Roboto", Arial, sans-serif;
  }
  .brand {
    position: absolute;
    right: 52px;
    top: 118px;
    text-align: right;
  }
  .brand-name {
    display: block;
    font-family: "Roboto Condensed", "Arial Narrow", sans-serif;
    font-weight: 700;
    font-size: 54px;
    line-height: 60px;
    color: var(--brand-blue);
    letter-spacing: 1px;
  }
  .brand-tagline {
    display: block;
    margin-top: 14px;
    font-family: "Roboto", Arial, sans-serif;
    font-weight: 500;
    font-size: 18px;
    letter-spacing: 3.4px;
    color: var(--brand-orange);
    margin-right: -3px;
  }
  .holder-name {
    position: absolute;
    right: 52px;
    top: 270px;
    margin: 0;
    font-family: "Roboto Condensed", "Arial Narrow", sans-serif;
    font-weight: 700;
    font-size: 25px;
    color: var(--brand-blue);
    letter-spacing: 0.3px;
  }
  .contact-list {
    position: absolute;
    right: 52px;
    top: 316px;
    margin: 0;
    padding: 0;
    list-style: none;
  }
  .contact-list li {
    display: flex;
    justify-content: flex-end;
    align-items: center;
    height: 24px;
    font-size: 16.5px;
    color: var(--text-grey);
  }
  .contact-icon {
    width: 16px;
    height: 16px;
    margin-left: 9px;
    fill: var(--brand-blue);
  }
  .divider {
    position: absolute;
    left: 482px;
    top: 345px;
    width: 1px;
    height: 43px;
    background: var(--rule-grey);
  }
  .postal-address {
    position: absolute;
    right: 299px;
    top: 343px;
    text-align: right;
    font-style: normal;
    font-size: 16.5px;
    line-height: 23px;
    color: var(--text-grey);
  }
</style>
</head>
<body>
  <div class="business-card">
    <div class="brand">
      <span class="brand-name">QUORV</span>
      <span class="brand-tagline">INTERNATIONAL</span>
    </div>

    <h1 class="holder-name">DENNIS MORVALE</h1>

    <address class="postal-address">P.O. Box 872<br>Fernlow QLD 4309</address>
    <div class="divider"></div>

    <ul class="contact-list">
      <li>+61 487215963
        <svg class="contact-icon" viewBox="0 0 16 16" aria-hidden="true"><path d="M3.2 1.5l2.2-.4 1.3 3.2-1.5 1.1c.7 1.7 2 3 3.7 3.8l1.1-1.5 3.2 1.3-.4 2.3c-.2.8-.9 1.2-1.7 1.1C6.4 12 3.4 8.9 2.2 3.3c-.1-.8.3-1.6 1-1.8z"/></svg>
      </li>
      <li>dennis@quorv.com.au
        <svg class="contact-icon" viewBox="0 0 16 16" aria-hidden="true"><path d="M1 3.5h14v.8L8 8.6 1 4.3z"/><path d="M1 5.6l7 4.3 7-4.3v6.9H1z"/></svg>
      </li>
      <li>www.quorv.com.au
        <svg class="contact-icon" viewBox="0 0 16 16" aria-hidden="true"><circle cx="8" cy="8" r="7"/><path d="M5 4.5c1.2-.6 2.5 0 2.3 1.2-.2 1-1.6 1-1.4 2.2.2 1 1.5 1.1 1.3 2.4L6.6 12.5C5 11 4 9 4.4 6.8zM9.6 3.2c1.4.3 2.8 1.4 3 3-1 .2-1.6-.6-2.5-.4-.8.2-1.5-.3-1.3-1.1z" fill="#f4f4f4"/></svg>
      </li>
    </ul>
  </div>
</body>
</html>
```